Ringordner
Zielgruppe
Wir sind ein ambulanter Pflegedienst, der im Raum Dessau-Roßlau tätig ist. Wir haben uns mit einer Tagespflege erweitert. Zukünftig ist es geplant, dass wir uns um eine Therapie erweitern. Unsere Zielgruppe sind sämtliche Pflegebedürftige und deren Angehörige. Für die aktuelle Maßnahme sind jedoch die zukünftigen Mitarbeiter im Vordergrund.
Aufgabenstellung
Ich möchte für unsere zukünftigen Mitarbeiter einen A4 Ringordner mit zwei Klammern gestalten. Dieser Ordner wird als Willkomm Mappe für neue Mitarbeiter bei der Aufnahme der Tätigkeit übergeben. Das Design sollte das Hauptlogo des Pflegedienstes enthalten und auf die Tochterfirmen hinweisen. Es sollte modern und frisch wirken und vor allem professionell. Es soll die Mitarbeiter in unserer neuen Firma willkommen heißen.
Dann benötige ich ein zweites Design, dass für die Kunden ist. Es beinhaltet einen Leitfaden, was für die Zusammenarbeit zwischen Pflegedienst und Patient am wichtigsten ist. Dieses Design ist genauso wie beim Mitarbeiter ein A4 Ringordner mit zwei Klammern. Auch dieser Ordner soll diesmal den Patienten bekommen heißen. Hier soll auch das Logo des Pflegedienstes enthalten sein und auch die Tochterfirmen hinweisen.

```html
<!DOCTYPE html>
<html lang="de">
<head>
<meta charset="utf-8">
<title>Team Velora – Ordner</title>
<link rel="stylesheet" href="https://fonts.googleapis.com/css2?family=Gilda+Display&family=Raleway:wght@500;600&display=swap">
<style>
  :root{
    --page:#efeff0;
    --paper:#ffffff;
    --ink:#5a5a5c;
    --ink-soft:#6e6e70;
    --teal:#2e8f93;
    --teal-light:#aedcd9;
    --mint:#dcefeb;
    --peach:#f2b27a;
    --photo-a:#c9c3bb;
    --photo-b:#8aa3b8;
    --photo-c:#d6dadd;
    --photo-d:#9ea3a6;
  }
  *{margin:0;padding:0;box-sizing:border-box}
  html,body{width:885px;height:1200px;overflow:hidden;background:var(--page)}
  .binder-cover{
    position:absolute;left:0;top:341px;width:885px;height:518px;
    background:linear-gradient(to bottom,var(--paper) 0,var(--paper) 300px,var(--mint) 435px);
    font-family:"Raleway",sans-serif;color:var(--ink);overflow:hidden;
  }
  .photo-layer{position:absolute;left:0;top:0;width:885px;height:260px}
  .block{position:absolute;text-align:center}
  .back-panel{left:8px;width:400px}
  .front-panel{left:485px;width:400px}
  .brand-dot{width:46px;height:46px;border-radius:50%;border:3px solid var(--teal);margin:0 auto 12px}
  .brand-name{font-size:19px;font-weight:600;letter-spacing:.5px;color:var(--ink)}
  .partners{display:flex;justify-content:center;gap:22px;align-items:center}
  .partner{display:flex;align-items:center;gap:6px;font-size:9.5px;font-weight:600;white-space:nowrap}
  .partner .mark{width:14px;height:14px;border-radius:50%;flex:none}
  .partner.therapy{color:var(--teal)}
  .partner.therapy .mark{background:var(--teal)}
  .partner.daycare{color:var(--peach)}
  .partner.daycare .mark{background:var(--peach)}
  .display{font-family:"Gilda Display",serif;color:var(--ink);line-height:1}
  .slogan{font-size:25px}
  .welcome{font-size:37px;line-height:1.05}
  .subline{font-size:18px;margin-top:6px;color:var(--ink-soft)}
  .footer{
    position:absolute;left:0;top:435px;width:885px;height:68px;background:var(--paper);
  }
  .footer .col{position:absolute;top:19px;font-size:6.3px;line-height:9px;color:var(--ink-soft);font-weight:500;white-space:nowrap}
  .footer .mini-dot{position:absolute;left:427px;top:19px;width:30px;height:30px;border-radius:50%;border:2px solid var(--teal)}
  .footer .partners{position:absolute;left:485px;width:400px;top:27px}
  .accent-strip{position:absolute;left:0;top:503px;width:885px;height:12px;background:var(--teal-light)}
</style>
</head>
<body>
<section class="binder-cover">
  <svg class="photo-layer" viewBox="0 0 885 260" width="885" height="260">
    <defs>
      <linearGradient id="teamPhoto" x1="0" y1="0" x2="1" y2="1">
        <stop offset="0" stop-color="var(--photo-a)"/>
        <stop offset="1" stop-color="var(--photo-b)"/>
      </linearGradient>
      <linearGradient id="handPhoto" x1="0" y1="0" x2="1" y2="1">
        <stop offset="0" stop-color="var(--photo-c)"/>
        <stop offset="1" stop-color="var(--photo-d)"/>
      </linearGradient>
    </defs>
    <path role="img" aria-label="Foto: mehrere Hände übereinander, Gemeinschaft von Pflegekräften und Senioren" d="M0 0H400V202C280 196 120 150 0 124Z" fill="url(#teamPhoto)"/>
    <path role="img" aria-label="Foto: Hand einer Pflegekraft auf der Hand eines Seniors am Rollator" d="M400 0H885V225C760 225 560 214 400 202Z" fill="url(#handPhoto)"/>
    <circle cx="685" cy="230" r="52" fill="var(--paper)"/>
  </svg>

  <div class="block back-panel" style="top:198px">
    <div class="brand-dot"></div>
    <div class="brand-name">TEAM VELORA</div>
  </div>
  <div class="block back-panel" style="top:318px">
    <div class="partners">
      <span class="partner therapy"><span class="mark"></span>TEAM VELORA THERAPIE</span>
      <span class="partner daycare"><span class="mark"></span>Tagespflege Haus Amalinde</span>
    </div>
  </div>
  <div class="block back-panel display slogan" style="top:374px">Wir sind für Sie da!</div>

  <div class="block front-panel" style="top:198px">
    <div class="brand-dot"></div>
    <div class="brand-name">TEAM VELORA</div>
  </div>
  <div class="block front-panel" style="top:312px">
    <div class="display welcome">Herzlich<br>Willkommen</div>
    <div class="display subline">Ihre Unterlagen</div>
  </div>

  <footer class="footer">
    <div class="col" style="left:35px">Team Velora GmbH<br>Geschäftsführerin:<br>Lena Tobrindel</div>
    <div class="col" style="left:157px">Lindenweg 14<br>06800 Auenstadt<br>Deutschland</div>
    <div class="col" style="left:268px">030 / 41 27 93<br>info@team-velora.de<br>www.team-velora.de</div>
    <div class="mini-dot"></div>
    <div class="partners">
      <span class="partner therapy"><span class="mark"></span>TEAM VELORA THERAPIE</span>
      <span class="partner daycare"><span class="mark"></span>Tagespflege Haus Amalinde</span>
    </div>
  </footer>
  <div class="accent-strip"></div>
</section>
</body>
</html>
```